design a construction company business card

Design business card around our logo. Card must have all the typical info: name, title, address, phone, email, business name, etc. Somewhere on the card I would like to see our motto "Built on integrity... Inspired by commitment." Consider adding a splash of bright orange to the card to complement the blues and silvers/grays in the logo. We are open to metallic inks, textures, etc. We would like to see options on both light and dark backgrounds. The font in the logo is Euro Technic Extended Regular.

```html
<!DOCTYPE html>
<html lang="en">
<head>
<meta charset="utf-8">
<title>Hollis Building Co. — Business Card</title>
<link href="https://fonts.googleapis.com/css2?family=Montserrat:wght@400;500;700&display=swap" rel="stylesheet">
<style>
  :root {
    --bg: #1b1b1d;
    --card-light: #ffffff;
    --card-dark: #1e1e20;
    --brand-blue: #2a6fc9;
    --deep-blue: #2b3a9e;
    --steel: #8c8f94;
    --silver: #c9cbce;
    --ink: #6d6f73;
    --rule: #8a8a8a;
  }
  * { box-sizing: border-box; margin: 0; padding: 0; }
  html, body { width: 1200px; height: 960px; overflow: hidden; }
  body {
    background: var(--bg);
    font-family: "Montserrat", sans-serif;
    display: flex;
    align-items: center;
    justify-content: center;
    gap: 50px;
  }
  .card {
    position: relative;
    width: 525px;
    height: 300px;
    overflow: hidden;
    box-shadow: 0 20px 40px rgba(0,0,0,.55);
  }

  /* Front */
  .card-front { background: var(--card-light); }
  .brand { position: absolute; left: 40px; top: 44px; }
  .brand-name {
    display: flex; align-items: center; gap: 10px;
    font-weight: 700; font-size: 34px; letter-spacing: 3px;
    color: var(--brand-blue); line-height: 1;
  }
  .brand-mark { width: 14px; height: 14px; background: var(--brand-blue); }
  .brand-sub {
    margin-top: 6px; margin-left: 24px;
    font-size: 11px; letter-spacing: 3px; color: var(--steel);
  }
  .divider {
    position: absolute; left: 28px; right: 28px; top: 142px;
    height: 1px; background: var(--rule);
  }
  .contact {
    position: absolute; left: 34px; top: 178px;
    list-style: none; font-size: 12.5px; color: var(--ink);
  }
  .contact li { display: flex; align-items: center; gap: 9px; line-height: 17px; }
  .contact svg { width: 11px; height: 11px; fill: var(--brand-blue); flex: none; }
  .person {
    position: absolute; right: 40px; top: 166px; text-align: right;
  }
  .person-name {
    font-weight: 700; font-size: 22px; letter-spacing: 1.5px; color: var(--brand-blue);
  }
  .person-title { font-size: 12px; color: var(--ink); margin-top: 1px; }
  .address {
    margin-top: 14px; font-size: 12px; line-height: 16px; color: var(--ink);
  }
  .band {
    position: absolute; left: 0; right: 0; bottom: 0; height: 12px; display: flex;
  }
  .band-blue { width: 63%; background: linear-gradient(90deg, var(--brand-blue), var(--deep-blue)); }
  .band-gray { flex: 1; background: #a3a5a8; }

  /* Back */
  .card-back {
    background: radial-gradient(ellipse at 60% 30%, #2c2c2f 0%, var(--card-dark) 70%);
    display: flex; flex-direction: column; align-items: center; justify-content: center;
  }
  .back-brand {
    display: flex; align-items: center; gap: 12px;
    font-weight: 700; font-size: 40px; letter-spacing: 4px; color: var(--silver);
  }
  .back-brand .brand-mark { width: 16px; height: 16px; background: var(--silver); }
  .back-sub { margin-top: 8px; font-size: 12px; letter-spacing: 3px; color: var(--steel); }
  .motto {
    margin-top: 34px; font-size: 12px; letter-spacing: .5px; color: var(--silver);
  }
</style>
</head>
<body>
  <section class="card card-front" aria-label="Card front">
    <div class="brand">
      <div class="brand-name"><span class="brand-mark"></span>HOLLIS</div>
      <div class="brand-sub">— BUILDING CO. —</div>
    </div>
    <div class="divider"></div>
    <ul class="contact">
      <li><svg viewBox="0 0 24 24"><path d="M6.6 10.8a15.1 15.1 0 0 0 6.6 6.6l2.2-2.2a1 1 0 0 1 1-.25 11.4 11.4 0 0 0 3.6.57 1 1 0 0 1 1 1V20a1 1 0 0 1-1 1A17 17 0 0 1 3 4a1 1 0 0 1 1-1h3.5a1 1 0 0 1 1 1c0 1.25.2 2.45.57 3.57a1 1 0 0 1-.25 1z"/></svg>123-456-2100</li>
      <li><svg viewBox="0 0 24 24"><path d="M2 5h20v14H2zm2 2v.5l8 5 8-5V7z"/></svg>youremail@gmail.com</li>
      <li><svg viewBox="0 0 24 24"><circle cx="12" cy="12" r="10"/></svg>www.yourwebsite.com</li>
    </ul>
    <div class="person">
      <div class="person-name">YOUR NAME</div>
      <div class="person-title">Your Title</div>
      <div class="address">Your address<br>city<br>state, ZIP 0000</div>
    </div>
    <div class="band"><div class="band-blue"></div><div class="band-gray"></div></div>
  </section>

  <section class="card card-back" aria-label="Card back">
    <div class="back-brand"><span class="brand-mark"></span>HOLLIS</div>
    <div class="back-sub">— BUILDING CO. —</div>
    <div class="motto">Built on integrity... Inspired by commitment</div>
  </section>
</body>
</html>
```